Thornvale Group needs a business card design

We need a new business card design using the logo recently selected in a logo competition on Pixel Bazaar. Our business is a consultancy specializing in aviation and energy and the winning business card design will promote an image of precision and professionalism with creativity.

Please use the logo with the name on the front of the card and use a complementary font. Make the back white with either the light grey or dark grey logo.

Target Market(s)

Senior finance and legal leaders at aviation and energy companies

Industry/Entity Type

Management Consulting

Contact Information for Business Card

Peter Castrell
President
Thornvale Group

www.thornvalegroup.example

(555) 204-6391
pc@thornvalegroup.example

Requirements
Must have
• Professional font that goes well with the logo font

```html
<!DOCTYPE html>
<html lang="en">
<head>
<meta charset="utf-8">
<title>Thornvale Group — Business Card</title>
<link rel="stylesheet" href="https://fonts.googleapis.com/css2?family=Open+Sans:wght@400;700&family=Raleway:wght@400&display=swap">
<style>
  :root {
    --page: #e9e7e4;
    --card-white: #ffffff;
    --grey-dark: #4b4e53;
    --grey-light: #9a9da1;
    --blue-deep: #1f4f7c;
    --blue-mid: #3e73a3;
    --brand-blue: #2c5a82;
    --text-white: #ffffff;
    --title-blue: #a9cdf0;
    --marker-blue: #3d78b0;
    --shadow: rgba(0,0,0,0.18);
  }
  * { margin: 0; padding: 0; box-sizing: border-box; }
  html, body { width: 1200px; height: 913px; overflow: hidden; background: var(--page); }
  .stage { position: relative; width: 1200px; height: 913px; }

  .card {
    position: absolute;
    width: 525px;
    height: 300px;
    background: var(--card-white);
    box-shadow: 0 10px 28px var(--shadow);
    overflow: hidden;
  }
  .card--front { left: 70px; top: 110px; }
  .card--back  { left: 605px; top: 500px; }

  .front-panels { position: absolute; inset: 0; width: 100%; height: 100%; }

  .contact {
    position: absolute;
    left: 30px;
    top: 110px;
    color: var(--text-white);
    font-family: "Open Sans", sans-serif;
  }
  .contact__head { display: flex; align-items: stretch; gap: 10px; margin-bottom: 14px; }
  .contact__marker { width: 16px; background: var(--card-white); border-right: 4px solid var(--marker-blue); }
  .contact__name { font-weight: 700; font-size: 21px; line-height: 1.1; }
  .contact__title { font-size: 13px; color: var(--title-blue); font-weight: 400; line-height: 1.4; }
  .contact__list { list-style: none; padding-left: 26px; font-size: 13px; line-height: 1.55; }
  .contact__list li { display: flex; align-items: center; gap: 7px; }
  .contact__list svg { width: 10px; height: 10px; fill: var(--text-white); flex: none; }

  .brand {
    position: absolute;
    font-family: "Raleway", sans-serif;
    font-weight: 400;
    color: var(--brand-blue);
    text-align: center;
    line-height: 1;
    white-space: nowrap;
  }
  .brand__mark { display: inline-block; width: 14px; height: 14px; background: var(--brand-blue); margin-bottom: 12px; }
  .brand__word { display: block; }
  .brand__sub { display: block; letter-spacing: 0.9em; margin-top: 8px; padding-left: 0.9em; }

  .card--front .brand { left: 338px; top: 112px; width: 172px; }
  .card--front .brand__word { font-size: 26px; letter-spacing: 0.02em; }
  .card--front .brand__sub { font-size: 11px; }

  .card--back .brand { left: 0; right: 0; top: 98px; }
  .card--back .brand__word { font-size: 52px; letter-spacing: 0.02em; }
  .card--back .brand__sub { font-size: 18px; }
</style>
</head>
<body>
<main class="stage">

  <section class="card card--front" aria-label="Business card front">
    <svg class="front-panels" viewBox="0 0 525 300" preserveAspectRatio="none" aria-hidden="true">
      <defs>
        <linearGradient id="grey-panel" x1="0" y1="1" x2="1" y2="0">
          <stop offset="0" stop-color="#4b4e53"/>
          <stop offset="1" stop-color="#9a9da1"/>
        </linearGradient>
        <linearGradient id="blue-wedge" x1="0" y1="1" x2="1" y2="0">
          <stop offset="0" stop-color="#1f4f7c"/>
          <stop offset="1" stop-color="#3e73a3"/>
        </linearGradient>
      </defs>
      <polygon points="0,0 280,0 210,300 0,300" fill="url(#grey-panel)"/>
      <polygon points="280,0 292,0 330,300 210,300" fill="url(#blue-wedge)"/>
    </svg>

    <div class="contact">
      <div class="contact__head">
        <span class="contact__marker"></span>
        <div>
          <div class="contact__name">Peter Castrell</div>
          <div class="contact__title">President</div>
        </div>
      </div>
      <ul class="contact__list">
        <li><svg viewBox="0 0 10 10"><path d="M2 0h2l1 3-1.5 1a6 6 0 0 0 2.5 2.5L7 5l3 1v2a2 2 0 0 1-2 2A8 8 0 0 1 0 2a2 2 0 0 1 2-2z"/></svg>(555) 204-6391</li>
        <li><svg viewBox="0 0 10 10"><path d="M0 2h10v6H0zM1 3v.3l4 2.5 4-2.5V3L5 5.5z" fill-rule="evenodd"/></svg>pc@thornvalegroup.example</li>
        <li><svg viewBox="0 0 10 10"><circle cx="5" cy="5" r="5"/></svg>www.thornvalegroup.example</li>
      </ul>
    </div>

    <div class="brand">
      <span class="brand__mark"></span>
      <span class="brand__word">THORNVALE</span>
      <span class="brand__sub">GROUP</span>
    </div>
  </section>

  <section class="card card--back" aria-label="Business card back">
    <div class="brand">
      <span class="brand__mark"></span>
      <span class="brand__word">THORNVALE</span>
      <span class="brand__sub">GROUP</span>
    </div>
  </section>

</main>
</body>
</html>
```